Professional Package for CPA Firm

We would like a stationery design for our new CPA Firm based in Atlanta, GA called 'Vale 8'. We work with investors to help grow investments, tax free. We would like the design to have a professional/minimal look with a 'wow' factor. We need 9.5″ x 4.125″, 9x12, and 10x13 mailing envelopes, business cards, and a letterhead. We have a logo that is already complete. For the letterhead, we would like to have space to put credentials at the bottom of the page

Industry/Entity Type

CPA, Accounting

```html
<!DOCTYPE html>
<html lang="en">
<head>
<meta charset="utf-8">
<title>Vale 8 — Business Card</title>
<link href="https://fonts.googleapis.com/css2?family=Open+Sans:wght@400;700&display=swap" rel="stylesheet">
<style>
  :root {
    --page-bg: #e7e3dc;
    --panel-dark: #1c232b;
    --panel-mid: #27313b;
    --frost-light: #eceae6;
    --frost-mid: #d6d3cd;
    --teal: #2a7d84;
    --teal-deep: #1f5f63;
    --red: #d92027;
    --text-light: #c9ced3;
    --ink: #14171a;
  }
  * { margin: 0; padding: 0; box-sizing: border-box; }
  html, body { width: 1200px; height: 969px; overflow: hidden; }
  body {
    background: var(--page-bg);
    font-family: "Open Sans", Arial, sans-serif;
  }
  .business-card {
    position: absolute;
    left: 60px;
    top: 176px;
    width: 1080px;
    height: 616px;
    border-radius: 30px;
    overflow: hidden;
    background: linear-gradient(135deg, var(--frost-light) 0%, var(--frost-mid) 100%);
    box-shadow: 0 10px 30px rgba(0,0,0,0.18);
  }
  .card-shape { position: absolute; inset: 0; }
  .contact-block {
    position: absolute;
    left: 92px;
    top: 160px;
    color: var(--text-light);
  }
  .holder-name {
    font-size: 32px;
    font-weight: 400;
    letter-spacing: 0.5px;
    color: var(--teal);
    line-height: 40px;
  }
  .holder-title {
    font-size: 23px;
    color: var(--red);
    line-height: 30px;
  }
  .postal-address {
    margin-top: 16px;
    font-size: 23px;
    font-style: normal;
    line-height: 30px;
  }
  .contact-list {
    list-style: none;
    margin-top: 18px;
  }
  .contact-list li {
    display: flex;
    align-items: center;
    font-size: 23px;
    line-height: 31px;
  }
  .contact-icon {
    width: 18px;
    height: 18px;
    margin-right: 14px;
    fill: var(--red);
  }
  .brand-name {
    position: absolute;
    left: 640px;
    top: 318px;
    width: 360px;
    text-align: center;
    font-size: 74px;
    font-weight: 700;
    letter-spacing: 4px;
    color: var(--ink);
  }
</style>
</head>
<body>
  <section class="business-card">
    <svg class="card-shape" width="1080" height="616" viewBox="0 0 1080 616">
      <defs>
        <linearGradient id="panelShade" x1="0" y1="0" x2="0.6" y2="1">
          <stop offset="0" stop-color="#2a323b"/>
          <stop offset="0.5" stop-color="#141a20"/>
          <stop offset="1" stop-color="#27313b"/>
        </linearGradient>
      </defs>
      <path d="M0 0 H636 L470 320 Q456 350 470 380 L580 616 H0 Z" fill="none" stroke="var(--red)" stroke-width="6" transform="translate(10 0)"/>
      <path d="M0 0 H636 L470 320 Q456 350 470 380 L580 616 H0 Z" fill="var(--teal-deep)" transform="translate(4 0)"/>
      <path d="M0 0 H636 L470 320 Q456 350 470 380 L580 616 H0 Z" fill="url(#panelShade)"/>
    </svg>

    <div class="contact-block">
      <h1 class="holder-name">DANIEL REYES</h1>
      <p class="holder-title">President</p>
      <address class="postal-address">4120 Birchwood Lane<br>Fairview, Georgia 30418</address>
      <ul class="contact-list">
        <li>
          <svg class="contact-icon" viewBox="0 0 24 24"><path d="M6.6 10.8a15 15 0 0 0 6.6 6.6l2.2-2.2a1 1 0 0 1 1-.25 11.4 11.4 0 0 0 3.6.57 1 1 0 0 1 1 1V20a1 1 0 0 1-1 1A17 17 0 0 1 3 4a1 1 0 0 1 1-1h3.5a1 1 0 0 1 1 1c0 1.25.2 2.45.57 3.57a1 1 0 0 1-.25 1z"/></svg>
          555-214-7730
        </li>
        <li>
          <svg class="contact-icon" viewBox="0 0 24 24"><path d="M7 1h10a2 2 0 0 1 2 2v18a2 2 0 0 1-2 2H7a2 2 0 0 1-2-2V3a2 2 0 0 1 2-2zm0 3v15h10V4zm4 16.2a1 1 0 1 0 2 0 1 1 0 0 0-2 0z"/></svg>
          555-860-3145
        </li>
        <li>
          <svg class="contact-icon" viewBox="0 0 24 24"><path d="M3 6h18v12H3z M3 6l9 7 9-7" fill="var(--red)"/><path d="M4 7l8 6 8-6" fill="none" stroke="#1c232b" stroke-width="1.6"/></svg>
          info@vale8.com
        </li>
        <li>
          <svg class="contact-icon" viewBox="0 0 24 24"><circle cx="12" cy="12" r="10"/><path d="M7 9c2-1 3 1 5 0s2 2 1 3-3 1-3 3 2 3 0 4" fill="none" stroke="#1c232b" stroke-width="1.6"/></svg>
          www.vale8.com
        </li>
      </ul>
    </div>

    <p class="brand-name">VALE 8</p>
  </section>
</body>
</html>
```